Zielgruppe
Wir sind ein gemischter Chor aus der Schweiz unsere Mitglieder sind zwischen 20 und 70 Jahre jung und singen Querbeet durch die Musik von Drummel bis Lantern.
Weitere Infos www.wolkenstimmen-beispiel.ch
Aufgabenstellung
Für unser Konzert mit dem Titel " Glanzlichter Wolkenstimmen" brauchen wir für den Flyer ein Vorderseite Design. Das Konzertprogramm beinhaltet folgende Lieder:
Morgenlicht/ Varga, Bretonischer Nebel / Kai Wettbrand, Mai più qui/ Tilda,Ron+Asta, Falkachtal / Rolk,Beneath the willow/ Gaukler von Tamr, Anyone to hold/Lantern, Falling of the elk/ trad. Irl.,Danse ma rivière/trad CH,Won't you keep the fire burning bright/ Bram Feldway, Alba del mar/Driftkey, Follow the Thunder/Al Brenning.
Idealerweise nimmt das Design Bezug auf den Titel oder auf eines oder mehrere Lieder.
Format: A5 hoch
Text: "Glanzlichter Wolkenstimmen"
Samstag 7. November 2015
17.00 Uhr, Singsaal Talwacht, Uerikon / Stäfa
Sonntag 8. November 2015
17.00 Uhr Kornhaldensaal, Uetikon am See
Eintritt frei Kollekte

```html
<!DOCTYPE html>
<html lang="de">
<head>
<meta charset="utf-8">
<title>Glanzlichter Wolkenstimmen – Flyer</title>
<link rel="stylesheet" href="https://fonts.googleapis.com/css2?family=Lobster&family=Signika:wght@700&family=Open+Sans:wght@400&family=Crimson+Text:ital@1&display=swap">
<style>
  :root {
    --navy: #0b2a6e;
    --blue: #1f4fae;
    --blue-light: #3d7fd6;
    --green: #9cc21a;
    --green-dark: #6f9a0c;
    --green-light: #c4dc4c;
    --white: #ffffff;
    --song-ink: #a9bbe0;
  }
  html, body { margin: 0; padding: 0; overflow: hidden; background: #fff; }
  .flyer {
    position: relative;
    width: 829px;
    height: 1200px;
    overflow: hidden;
    background: radial-gradient(ellipse at 40% 55%, var(--blue-light) 0%, var(--blue) 40%, var(--navy) 88%);
    font-family: "Open Sans", sans-serif;
  }
  .photo-strip {
    position: absolute; left: 0; top: 0; width: 829px; height: 128px;
    display: flex; gap: 5px; background: #fff;
  }
  .photo { height: 100%; }
  .photo--band   { flex: 0 0 160px; background: linear-gradient(160deg, #4e6a78 0%, #3b3a36 55%, #6d5a48 100%); }
  .photo--crowd  { flex: 0 0 232px; background: linear-gradient(180deg, #7d5a4a 0%, #b79d8a 45%, #4c4640 100%); }
  .photo--choir  { flex: 0 0 240px; background: linear-gradient(180deg, #9a8472 0%, #c9a784 45%, #6f5d6e 100%); }
  .photo--singer { flex: 1; background: linear-gradient(180deg, #8c7968 0%, #ded4c8 50%, #3a3534 100%); }
  .backdrop-word {
    position: absolute; left: 20px; top: 120px; margin: 0;
    font-family: "Signika", sans-serif; font-weight: 700; font-size: 300px;
    color: rgba(255,255,255,.06); letter-spacing: 4px; line-height: 1;
  }
  .star { position: absolute; }
  .title-small {
    position: absolute; left: 155px; top: 222px; margin: 0;
    font-family: "Signika", sans-serif; font-weight: 700; font-size: 34px;
    color: var(--white);
  }
  .title-main {
    position: absolute; left: 52px; top: 238px; margin: 0;
    font-family: "Lobster", cursive; font-weight: 400; font-size: 110px;
    color: var(--green); line-height: 1.1;
  }
  .illustration { position: absolute; }
  .illustration--clef {
    left: 80px; top: 390px; width: 360px; height: 340px;
    background: radial-gradient(ellipse at 45% 50%, rgba(255,255,255,.62) 0%, rgba(255,255,255,.28) 40%, rgba(255,255,255,0) 70%);
  }
  .illustration--figure {
    left: 420px; top: 345px; width: 300px; height: 310px;
    background: radial-gradient(ellipse at 50% 50%, rgba(255,255,255,.7) 0%, rgba(255,255,255,.3) 42%, rgba(255,255,255,0) 70%);
  }
  .songlist {
    position: absolute; left: 385px; top: 680px; width: 395px; margin: 0;
    font-family: "Crimson Text", serif; font-style: italic; font-size: 17px; line-height: 1.45;
    color: var(--song-ink);
    transform: rotate(-7deg); transform-origin: left top;
  }
  .ground { position: absolute; left: 0; top: 820px; width: 829px; height: 380px; }
  .date-block { position: absolute; left: 279px; }
  .date-block h2 {
    margin: 0; font-family: "Signika", sans-serif; font-weight: 700; font-size: 34px;
    color: var(--white); line-height: 1.1; letter-spacing: .5px;
  }
  .date-block p { margin: 6px 0 0; font-size: 18px; color: var(--white); line-height: 1.4; }
</style>
</head>
<body>
<main class="flyer">
  <div class="photo-strip">
    <div class="photo photo--band" role="img" aria-label="Foto: Musiker mit Akkordeon und Notenständer"></div>
    <div class="photo photo--crowd" role="img" aria-label="Foto: Chor auf der Bühne vor Publikum"></div>
    <div class="photo photo--choir" role="img" aria-label="Foto: Chor in farbigen Hemden in einer Kirche"></div>
    <div class="photo photo--singer" role="img" aria-label="Foto: Sänger mit Notenmappen"></div>
  </div>

  <p class="backdrop-word" aria-hidden="true">Best</p>

  <svg class="star" style="left:266px;top:184px" width="40" height="40" viewBox="0 0 24 24"><polygon points="12,1 15,9 23,9 16.5,14 19,22 12,17 5,22 7.5,14 1,9 9,9" fill="#fff"/></svg>
  <svg class="star" style="left:368px;top:354px" width="22" height="22" viewBox="0 0 24 24"><polygon points="12,1 15,9 23,9 16.5,14 19,22 12,17 5,22 7.5,14 1,9 9,9" fill="var(--green)"/></svg>
  <svg class="star" style="left:706px;top:324px" width="40" height="40" viewBox="0 0 24 24"><polygon points="12,1 15,9 23,9 16.5,14 19,22 12,17 5,22 7.5,14 1,9 9,9" fill="#fff"/></svg>
  <svg class="star" style="left:326px;top:750px" width="38" height="38" viewBox="0 0 24 24"><polygon points="12,1 15,9 23,9 16.5,14 19,22 12,17 5,22 7.5,14 1,9 9,9" fill="var(--green)"/></svg>

  <p class="title-small">Glanzlichter</p>
  <h1 class="title-main">Wolkenstimmen</h1>

  <div class="illustration illustration--clef" role="img" aria-label="Illustration: weisser Violinschlüssel mit geschwungenem Notenband"></div>
  <div class="illustration illustration--figure" role="img" aria-label="Illustration: springende Figur als weisse Silhouette mit Notenlinien"></div>

  <p class="songlist">Morgenlicht| Varga, Bretonischer Nebel | Kai Wettbrand, Mai più qui | Tilda,Ron+Asta, Falkachtal | Rolk,Beneath the willow| Gaukler von Tamr, Anyone to hold|Lantern, Falling of the elk| trad. Irl.,Danse ma rivière|trad CH,Won't you keep the fire burning bright| Bram Feldway, Alba del mar|Driftkey, Follow the Thunder|Al Brenning.</p>

  <svg class="ground" viewBox="0 0 829 380" preserveAspectRatio="none" aria-hidden="true">
    <defs>
      <linearGradient id="grass" x1="0" y1="0" x2="0" y2="1">
        <stop offset="0" stop-color="var(--green)"/>
        <stop offset="1" stop-color="var(--green-dark)"/>
      </linearGradient>
    </defs>
    <path d="M0,90 C220,20 520,10 829,40 L829,380 L0,380 Z" fill="var(--green-light)"/>
    <path d="M0,112 C230,45 530,35 829,62 L829,380 L0,380 Z" fill="url(#grass)"/>
  </svg>

  <svg class="star" style="left:205px;top:978px" width="40" height="40" viewBox="0 0 24 24"><polygon points="12,1 15,9 23,9 16.5,14 19,22 12,17 5,22 7.5,14 1,9 9,9" fill="#fff"/></svg>
  <section class="date-block" style="top:966px">
    <h2>Samstag 7. November 2015</h2>
    <p>17.00 Uhr, Singsaal Talwacht, Uerikon / Stäfa</p>
  </section>

  <svg class="star" style="left:205px;top:1074px" width="40" height="40" viewBox="0 0 24 24"><polygon points="12,1 15,9 23,9 16.5,14 19,22 12,17 5,22 7.5,14 1,9 9,9" fill="#fff"/></svg>
  <section class="date-block" style="top:1064px">
    <h2>Sonntag 8. November 2015</h2>
    <p>17.00 Uhr Kornhaldensaal, Uetikon am See<br>Eintritt frei Kollekte</p>
  </section>
</main>
</body>
</html>
```